Business Card Design

New business card design

Target Market(s)

Residential & Commercial Property Managers

Industry/Entity Type

Plumbing Services

Contact Information for Business Card

Name - Rowan Keddle, title - Director, Phone Number - 0431 286 517, email - rowan@tbk-plumbing.com.au, Company ABN - 73 215 904 386,

Font styles to use
Sans Serif

Colors
0054AA
0677BA
7BADD7
CADEEF
E8F1F8

```html
<!DOCTYPE html>
<html lang="en">
<head>
<meta charset="utf-8">
<title>TBK Plumbing Services – Business Card</title>
<link href="https://fonts.googleapis.com/css2?family=Montserrat:wght@400;500;700&display=swap" rel="stylesheet">
<style>
  :root {
    --stage: #3a3a3c;
    --card-dark: #1f252c;
    --card-light: #ffffff;
    --ink: #1f252c;
    --ink-soft: #2b3138;
    --muted: #6d7279;
    --accent: #09a9ea;
    --accent-deep: #0677ba;
  }
  * { box-sizing: border-box; margin: 0; padding: 0; }
  html, body { width: 1200px; height: 689px; overflow: hidden; }
  body {
    background: var(--stage);
    font-family: "Montserrat", sans-serif;
    position: relative;
  }
  .card {
    position: absolute;
    top: 190px;
    width: 540px;
    height: 309px;
    border-radius: 22px;
    overflow: hidden;
    box-shadow: 0 14px 30px rgba(0,0,0,.35);
  }
  .card--front { left: 40px; background: var(--card-dark); }
  .card--back { left: 620px; background: var(--card-light); }

  /* wordmark */
  .wordmark {
    position: absolute;
    display: flex;
    align-items: center;
    gap: 14px;
  }
  .wordmark__dot {
    width: 18px; height: 18px; border-radius: 50%;
    background: var(--accent);
    flex: none;
  }
  .wordmark__text {
    font-weight: 400;
    line-height: 1;
  }
  .wordmark__name {
    display: block;
    letter-spacing: 4px;
  }
  .wordmark__tag {
    display: block;
    letter-spacing: 6px;
    margin-top: 10px;
  }
  .card--front .wordmark {
    left: 50%; top: 50%;
    transform: translate(-50%, -50%);
  }
  .card--front .wordmark__text { color: #ffffff; text-align: center; }
  .card--front .wordmark__name { font-size: 74px; }
  .card--front .wordmark__tag { font-size: 12px; }

  .card--back .wordmark { left: 30px; top: 96px; }
  .card--back .wordmark__text { color: var(--ink); }
  .card--back .wordmark__name { font-size: 58px; }
  .card--back .wordmark__tag { font-size: 10px; letter-spacing: 5px; }
  .card--back .wordmark__dot { width: 14px; height: 14px; }

  .divider {
    position: absolute;
    left: 262px; top: 58px;
    width: 1px; height: 128px;
    background: var(--muted);
  }

  .contact {
    position: absolute;
    left: 280px; top: 56px;
    color: var(--ink-soft);
  }
  .contact__name {
    font-weight: 700;
    font-size: 21px;
    color: var(--accent);
    line-height: 1.1;
  }
  .contact__title {
    font-size: 14px;
    margin-top: 4px;
    margin-bottom: 10px;
  }
  .contact__row {
    display: flex;
    align-items: center;
    gap: 8px;
    font-size: 12.5px;
    line-height: 1.7;
  }
  .contact__icon { width: 13px; height: 13px; flex: none; }
  .contact__abn { font-size: 12.5px; margin-top: 6px; }

  .band {
    position: absolute;
    left: 0; right: 0; bottom: 0;
    height: 62px;
    background: var(--card-dark);
    border-top: 4px solid var(--accent);
  }
  .band::before {
    content: "";
    position: absolute;
    left: 0; right: 0; top: -10px;
    height: 6px;
    background: var(--card-light);
  }
</style>
</head>
<body>

  <section class="card card--front" aria-label="Card front">
    <div class="wordmark">
      <span class="wordmark__text">
        <span class="wordmark__name">tbk</span>
        <span class="wordmark__tag">plumbing services</span>
      </span>
      <span class="wordmark__dot"></span>
    </div>
  </section>

  <section class="card card--back" aria-label="Card back">
    <div class="wordmark">
      <span class="wordmark__text">
        <span class="wordmark__name">tbk</span>
        <span class="wordmark__tag">plumbing services</span>
      </span>
      <span class="wordmark__dot"></span>
    </div>

    <div class="divider"></div>

    <div class="contact">
      <p class="contact__name">Rowan Keddle</p>
      <p class="contact__title">Director</p>
      <p class="contact__row">
        <svg class="contact__icon" viewBox="0 0 24 24" aria-hidden="true">
          <path fill="#09a9ea" d="M6.6 10.8a15.1 15.1 0 0 0 6.6 6.6l2.2-2.2c.3-.3.7-.4 1-.2 1.1.4 2.3.6 3.6.6.6 0 1 .4 1 1V20c0 .6-.4 1-1 1A17 17 0 0 1 3 4c0-.6.4-1 1-1h3.5c.6 0 1 .4 1 1 0 1.3.2 2.5.6 3.6.1.3 0 .7-.2 1z"/>
        </svg>
        0431 286 517
      </p>
      <p class="contact__row">
        <svg class="contact__icon" viewBox="0 0 24 24" aria-hidden="true">
          <rect x="2" y="5" width="20" height="14" rx="1.5" fill="#09a9ea"/>
          <path d="M3 6.5l9 6.5 9-6.5" fill="none" stroke="#ffffff" stroke-width="2"/>
        </svg>
        rowan@tbk-plumbing.com.au
      </p>
      <p class="contact__abn">ABN - 73 215 904 386</p>
    </div>

    <div class="band"></div>
  </section>

</body>
</html>
```